Business Intelligence Application - Reporting Menu and Report Criteria Design

Looking for a fresh, effective and user friendly view for the menu structure and reporting criteria screen format for a business reporting application. Initial format completed, content structure is in place, but we need the 'wow' design.. as its a serious professional report/BI tool it has to fall within certain guidelines for clarity and graphics..but we want it to be slick, friendly, great user experience. There is a large amount of complex content to fit into a small space and we need it to be very inviting, modern and intuitive.. If interested, please review the attachment. We have live screens in operation, but feel these could be improved and looking forward to seeing what great creative suggestions could be made. Please review work done to date in the attached.. We are not looking for a total re-design of everything, all the basic business content/structure is there.. but tell us what we could do to improve this in terms of graphic design... particularly the criteria screens.. thanks!
Updates

Reason: Need a few more days to review designs - thanks for all submissions so far, we will make a selection shortly.

Target Market(s)

Business analysts, hotel operations teams, finance analysts hospitality industry

Industry/Entity Type

Hospitality

Coding

Coded - Design and coding required

Number of Pages Required

4 page

Font styles to use
Sans Serif
Other font styles liked:
• Candara, please see example in deck

Colors
3276b5
3176b5
0255a3
85acd3
33a6d7
cee9f5
85cae6

Requirements
Must have
• sharp clear, logical menu structure, (currently it has 'clicks to sub-menus, we need hover over, slide to sub-menus..) colour, styling.. and most focus on revision of criteria.. right now is somewhat heavy, cumbersome.. keep colour and friendly intuitive process steps.. its heavy analytical stuff.. best of luck!
Should not have
• No grey fonts on white or grey screens! many business apps are not readable or sharp.. or fonts are too small.. colourless, so please avoid that.. see our deck - sharp dark (navy) or black fonts on white, or light shading..

```html
<!DOCTYPE html>
<html lang="en">
<head>
<meta charset="utf-8">
<title>Tidewater – Property Search</title>
<link href="https://fonts.googleapis.com/css2?family=Mulish:wght@400;600;700&display=swap" rel="stylesheet">
<style>
:root{
  --navy:#011634;
  --nav:#0255a3;
  --nav-dark:#0b4a8e;
  --tab-light:#4bb0df;
  --tab-admin:#2e8fcf;
  --menu:#2b8fcc;
  --menu-line:#5cb0dc;
  --menu-active:#0255a3;
  --panel:#55b4df;
  --body-top:#3aa3d9;
  --body-bottom:#0a5cab;
  --button:#0255a3;
  --footer:#e1e1e1;
  --footer-text:#6a6a6a;
  --white:#ffffff;
  --icon-blue:#1b7fc4;
  --field-text:#5a5a5a;
}
*{box-sizing:border-box;margin:0;padding:0}
html,body{width:1200px;height:664px;overflow:hidden}
body{font-family:"Mulish",sans-serif;background:var(--white);position:relative}
.header{position:absolute;left:0;top:0;width:1200px;height:113px;background:var(--navy)}
.brand{position:absolute;left:99px;top:38px;display:flex;align-items:center;gap:14px}
.brand-dot{width:36px;height:36px;border-radius:50%;background:var(--icon-blue)}
.brand-name{font-size:28px;font-weight:700;color:var(--white);letter-spacing:.2px}
.avatar{position:absolute;left:781px;top:34px;width:44px;height:44px;border-radius:50%;background:radial-gradient(circle at 50% 40%,#c9b7a4,#6b5c50)}
.welcome{position:absolute;left:833px;top:36px;color:var(--white);font-size:14px;line-height:21px}
.welcome strong{font-weight:600}
.divider{position:absolute;top:40px;width:1px;height:38px;background:#1d3556}
.header-icon{position:absolute}
.nav{position:absolute;left:0;top:113px;width:1200px;height:51px;background:var(--nav)}
.tab{position:absolute;top:0;height:51px;display:flex;align-items:center;gap:9px;color:var(--white);font-size:18px;font-weight:600;padding-left:22px}
.tab-admin{left:85px;width:129px;background:var(--tab-admin)}
.tab-management{left:214px;width:191px;background:var(--nav-dark);padding-left:27px}
.tab-search{left:406px;width:227px;background:var(--tab-light);padding-left:44px}
.tab-intel{left:634px;width:133px;padding-left:35px}
.tab-planning{left:768px;width:160px;padding-left:22px;border-left:1px solid #3f86c8}
.main{position:absolute;left:0;top:164px;width:1200px;height:424px;background:linear-gradient(var(--body-top),var(--body-bottom))}
.criteria-panel{position:absolute;left:112px;top:183px;width:974px;height:320px;background:var(--panel)}
.field-label{position:absolute;color:var(--white);font-size:17px;font-weight:700}
.field-label.plain{font-weight:600;font-size:18px}
.field{position:absolute;height:43px;background:linear-gradient(#ffffff,#ececec);border:1px solid #d5e6f1;font-size:16px;color:var(--field-text);padding:11px 17px}
.search-button{position:absolute;left:820px;top:416px;width:215px;height:51px;background:var(--button);color:var(--white);font-size:20px;font-weight:700;display:flex;align-items:center;justify-content:center;letter-spacing:.5px}
.dropdown{position:absolute;left:84px;top:164px;width:265px;height:173px;background:var(--menu);box-shadow:0 2px 6px rgba(0,0,0,.2)}
.dropdown-item{position:absolute;left:0;width:265px;color:var(--white);font-size:16px;padding-left:32px;display:flex;align-items:center;border-bottom:1px solid var(--menu-line)}
.dropdown-item.active{background:var(--menu-active);border-bottom:none;left:-2px;width:267px;padding-left:34px}
.dropdown-item.last{border-bottom:none}
.submenu{position:absolute;left:349px;top:245px;width:210px;height:258px;background:var(--menu-active);padding-top:22px}
.submenu-item{display:block;color:var(--white);font-size:14px;line-height:28.2px;padding-left:32px}
.footer{position:absolute;left:0;top:588px;width:1200px;height:76px;background:var(--footer);color:var(--footer-text);font-size:13px;text-align:center;padding-top:26px}
</style>
</head>
<body>
<header class="header">
  <div class="brand"><span class="brand-dot"></span><span class="brand-name">Tidewater</span></div>
  <div class="avatar" role="img" aria-label="Profile photo of the signed-in administrator"></div>
  <div class="welcome">Welcome<br><strong>Admin</strong></div>
  <span class="divider" style="left:919px"></span>
  <svg class="header-icon" style="left:947px;top:41px" width="27" height="30" viewBox="0 0 24 26" aria-hidden="true"><path fill="#1b7fc4" d="M12 0c1 0 1.8.8 1.8 1.8v.6C17.4 3.3 19.5 6.3 19.5 10v6l3 3.5v1.5h-21v-1.5l3-3.5v-6c0-3.7 2.1-6.7 5.7-7.6v-.6C10.2.8 11 0 12 0zM9 22.5h6a3 3 0 0 1-6 0z"/></svg>
  <span class="divider" style="left:1005px"></span>
  <svg class="header-icon" style="left:1036px;top:45px" width="28" height="24" viewBox="0 0 28 24" aria-hidden="true"><path fill="#1b7fc4" d="M17 0l11 10-11 10v-6C9 14 4 16 0 24 1 14 6 7 17 6z"/></svg>
</header>

<nav class="nav">
  <div class="tab tab-admin"><svg width="22" height="22" viewBox="0 0 22 22" aria-hidden="true"><circle cx="11" cy="6" r="5.5" fill="#fff"/><path d="M1 22c0-6 4-9 10-9s10 3 10 9z" fill="#fff"/></svg>Admin</div>
  <div class="tab tab-management"><svg width="28" height="22" viewBox="0 0 28 22" aria-hidden="true"><g fill="#fff"><rect x="10" y="0" width="8" height="7"/><rect x="0" y="15" width="8" height="7"/><rect x="10" y="15" width="8" height="7"/><rect x="20" y="15" width="8" height="7"/><rect x="13" y="7" width="2" height="8"/><rect x="3" y="10" width="22" height="2"/><rect x="3" y="10" width="2" height="5"/><rect x="23" y="10" width="2" height="5"/></g></svg>Management</div>
  <div class="tab tab-search"><svg width="20" height="20" viewBox="0 0 20 20" aria-hidden="true"><circle cx="8" cy="8" r="6" fill="none" stroke="#fff" stroke-width="3"/><path d="M12.5 12.5l6 6" stroke="#fff" stroke-width="3.5" stroke-linecap="round"/></svg>Property Search</div>
  <div class="tab tab-intel"><svg width="22" height="22" viewBox="0 0 22 22" aria-hidden="true"><circle cx="11" cy="11" r="11" fill="#fff"/><path d="M5 5c3 0 4 2 3 4s-3 2-2 5 1 4 0 5C3 17 2 12 4 7zM13 3c3 1 6 4 6 8-2 0-3-2-5-1s-1 4-3 4-1-4-2-6 2-3 4-5z" fill="#0255a3"/></svg>Intel</div>
  <div class="tab tab-planning"><svg width="24" height="24" viewBox="0 0 24 24" aria-hidden="true"><path fill="#fff" d="M10 0h4l.6 3.2 2.3 1 2.7-1.9 2.8 2.8-1.9 2.7 1 2.3L24 10v4l-3.2.6-1 2.3 1.9 2.7-2.8 2.8-2.7-1.9-2.3 1L14 24h-4l-.6-3.2-2.3-1-2.7 1.9-2.8-2.8 1.9-2.7-1-2.3L0 14v-4l3.2-.6 1-2.3-1.9-2.7 2.8-2.8 2.7 1.9 2.3-1zM12 8a4 4 0 1 0 0 8 4 4 0 0 0 0-8z"/></svg>Planning</div>
</nav>

<main class="main"></main>

<section class="criteria-panel" aria-label="Search criteria"></section>
<div class="field-label" style="left:460px;top:226px">SEARCH ID</div>
<div class="field-label" style="left:753px;top:226px">SEARCH PRODUCT</div>
<div class="field" style="left:340px;top:257px;width:398px"></div>
<div class="field" style="left:752px;top:257px;width:282px"></div>
<div class="field-label" style="left:158px;top:330px">DIVISIONS</div>
<div class="field-label plain" style="left:752px;top:325px">Areas</div>
<div class="field" style="left:157px;top:358px;width:283px">North Amercia</div>
<div class="field" style="left:440px;top:358px;width:298px"></div>
<div class="field" style="left:752px;top:358px;width:282px"></div>
<div class="search-button">SEARCH</div>

<div class="dropdown">
  <div class="dropdown-item" style="top:0;height:44px">Registration</div>
  <div class="dropdown-item" style="top:44px;height:37px">User Access</div>
  <div class="dropdown-item active" style="top:81px;height:38px">Setup</div>
  <div class="dropdown-item last" style="top:119px;height:37px">Data Imports</div>
</div>
<div class="submenu">
  <span class="submenu-item">Market Segments</span>
  <span class="submenu-item">Banquet &amp; Catering</span>
  <span class="submenu-item">Outlets/F&amp;B Service</span>
  <span class="submenu-item">Other Income</span>
  <span class="submenu-item">Impact Dates</span>
  <span class="submenu-item">Inventory</span>
  <span class="submenu-item">Geo/Location</span>
  <span class="submenu-item">Distribution Channels</span>
</div>

<footer class="footer">© 2017 Company Name&nbsp; All right reserved&nbsp; Term of Use</footer>
</body>
</html>
```